Social Media Graphics - Oakline Push REVISED

Create 6-7 individual social media graphics (square size) to encourage folks to join our online course called:

The Harvest Ledger Circle
How to Launch a Multi-Million Business From Scratch
Sign Up Today!

IMPORTANT: Make the largest and most prominent text on the graphic be: How to Launch a Multi-Million Business From Scratch

For the color scheme of the graphics, let's try a blue color palette; make sure the graphics appeal to both men and women

Make sure each graphic contains 1 of the 3 pics attached (crop pic as needed); and make sure one of the graphics is all TEXT only.

Target Market(s)

men and women looking to start a business

Industry/Entity Type

Entrepreneurship

Colors
0054AA
0677BA
7BADD7
CADEEF
E8F1F8

Requirements
Must have
• All the text and use the 3 pics provided; one graphic can be all text; Simple, modern design that's easy to read

```html
<!DOCTYPE html>
<html lang="en">
<head>
<meta charset="utf-8">
<title>The Harvest Ledger Circle – Sign Up Today</title>
<link rel="stylesheet" href="https://fonts.googleapis.com/css2?family=Anton&family=Bebas+Neue&display=swap">
<style>
  :root {
    --navy: #021a38;
    --paper: #ffffff;
    --blue-deep: #0054aa;
    --blue-mid: #0677ba;
    --blue-soft: #7badd7;
    --blue-pale: #cadeef;
    --blue-mist: #e8f1f8;
    --headline-accent: #7badd7;
    --cta-fill: #0677ba;
  }
  html, body {
    margin: 0;
    padding: 0;
    width: 1200px;
    height: 1200px;
    overflow: hidden;
    background: var(--navy);
  }
  .promo-tile {
    display: block;
    width: 1200px;
    height: 1200px;
  }
  .course-name {
    font-family: "Bebas Neue", "Anton", sans-serif;
    font-size: 86px;
    fill: var(--navy);
  }
  .headline-light {
    font-family: "Bebas Neue", "Anton", sans-serif;
    fill: var(--paper);
  }
  .headline-accent {
    font-family: "Anton", "Bebas Neue", sans-serif;
    fill: var(--headline-accent);
  }
  .cta-button {
    fill: var(--cta-fill);
    stroke: var(--paper);
    stroke-width: 3;
  }
  .cta-label {
    font-family: "Bebas Neue", "Anton", sans-serif;
    font-size: 80px;
    fill: var(--paper);
  }
  .cursor-arrow {
    fill: var(--navy);
    stroke: var(--paper);
    stroke-width: 3;
    stroke-linejoin: round;
  }
  .click-rays {
    stroke: var(--navy);
    stroke-width: 3.5;
    stroke-linecap: round;
    fill: none;
  }
</style>
</head>
<body>
<svg class="promo-tile" viewBox="0 0 1200 1200" xmlns="http://www.w3.org/2000/svg" role="img" aria-label="The Harvest Ledger Circle: How to launch a multi-million business from scratch. Sign up today!">
  <defs>
    <linearGradient id="blue-sheen" x1="0" y1="0" x2="1" y2="0">
      <stop offset="0" stop-color="var(--blue-soft)"/>
      <stop offset="0.18" stop-color="var(--blue-mist)"/>
      <stop offset="0.4" stop-color="var(--blue-pale)"/>
      <stop offset="0.58" stop-color="var(--blue-soft)"/>
      <stop offset="0.8" stop-color="var(--blue-mist)"/>
      <stop offset="1" stop-color="var(--blue-soft)"/>
    </linearGradient>
  </defs>

  <rect class="backdrop" width="1200" height="1200" fill="var(--navy)"/>

  <path class="top-band" d="M0 0 H1200 V117 Q600 340 0 117 Z" fill="url(#blue-sheen)"/>
  <path class="bottom-band" d="M0 1111 Q600 945 1200 1111 V1200 H0 Z" fill="url(#blue-sheen)"/>

  <text class="course-name" x="600" y="139" text-anchor="middle" textLength="640" lengthAdjust="spacingAndGlyphs">THE HARVEST LEDGER CIRCLE</text>

  <g class="headline">
    <text class="headline-light" x="133" y="418" font-size="218" textLength="934" lengthAdjust="spacingAndGlyphs">HOW TO LAUNCH</text>
    <text class="headline-accent" x="133" y="553" font-size="154" textLength="934" lengthAdjust="spacingAndGlyphs">A MULTI-MILLION</text>
    <text class="headline-light" x="133" y="802" font-size="326" textLength="934" lengthAdjust="spacingAndGlyphs">BUSINESS</text>
    <text class="headline-accent" x="133" y="944" font-size="162" textLength="934" lengthAdjust="spacingAndGlyphs">FROM SCRATCH!</text>
  </g>

  <g class="cta">
    <rect class="cta-button" x="398" y="978" width="394" height="100" rx="13"/>
    <text class="cta-label" x="595" y="1055" text-anchor="middle" textLength="352" lengthAdjust="spacingAndGlyphs">SIGN UP TODAY!</text>
    <g class="click-rays">
      <line x1="757" y1="1060" x2="753" y2="1046"/>
      <line x1="745" y1="1070" x2="733" y2="1064"/>
      <line x1="770" y1="1062" x2="778" y2="1050"/>
      <line x1="744" y1="1085" x2="732" y2="1090"/>
    </g>
    <path class="cursor-arrow" d="M756 1072 L756 1136 L771 1121 L782 1145 L793 1140 L782 1117 L803 1117 Z"/>
  </g>
</svg>
</body>
</html>
```